Card Design for my dog training business Brightpaw Obedience

Need a business card design for my dog training business with my new logo. Want the card to come off professional yet fun. Want it to be very eye catchy as well. I normally have these at vet clinics, pet stores, and groomers. so need it to look better than my competitors.
Target Market(s)
dog owners
Industry/Entity Type
Dog Training
Contact Information for Business Card
needs logo, my name and info
Font styles to use
Serif
Colors
0255a3
ffffff
ec1f27
000000
333333
fbfbfb
Requirements
Must have
- Brightpaw Obedience
- Felix Orland
- 415 903 2276
- info@brightpawobedience.example
- www.brightpawobedience.example

```html
<!DOCTYPE html>
<html lang="en">
<head>
<meta charset="utf-8">
<title>Brightpaw Obedience — Business Card</title>
<link rel="stylesheet" href="https://fonts.googleapis.com/css2?family=EB+Garamond:ital,wght@0,400;0,500;1,400&family=Montserrat:wght@400;700&display=swap">
<style>
  :root {
    --backdrop: #ececec;
    --card: #2f2f2f;
    --white: #ffffff;
    --red: #ec1f27;
    --muted: #d9d9d9;
    --rule: #6a6a6a;
  }
  * { box-sizing: border-box; margin: 0; padding: 0; }
  html, body { width: 1200px; height: 1200px; overflow: hidden; }
  body {
    background: var(--backdrop);
    display: flex;
    flex-direction: column;
    align-items: center;
    justify-content: center;
    gap: 60px;
  }
  .card {
    width: 840px;
    height: 480px;
    background: var(--card);
    position: relative;
    box-shadow: 0 10px 24px rgba(0,0,0,0.18);
  }

  /* Front */
  .card-front {
    display: flex;
    flex-direction: column;
    align-items: center;
    justify-content: center;
    gap: 90px;
    padding-top: 30px;
  }
  .brand {
    display: flex;
    align-items: center;
    gap: 18px;
  }
  .brand-dot {
    width: 22px;
    height: 22px;
    border-radius: 50%;
    background: var(--red);
    flex: none;
  }
  .brand-name {
    font-family: "EB Garamond", serif;
    font-weight: 500;
    font-size: 60px;
    letter-spacing: 1px;
    color: var(--white);
    white-space: nowrap;
  }
  .tagline {
    font-family: "EB Garamond", serif;
    font-style: italic;
    font-size: 26px;
    color: var(--white);
    white-space: nowrap;
  }

  /* Back */
  .card-back {
    display: flex;
    align-items: center;
    justify-content: center;
    padding-top: 40px;
  }
  .identity {
    text-align: right;
    padding-right: 26px;
    font-family: "Montserrat", sans-serif;
  }
  .identity-name {
    font-weight: 700;
    font-size: 30px;
    color: var(--red);
    text-transform: uppercase;
    white-space: nowrap;
  }
  .identity-role {
    font-weight: 400;
    font-size: 22px;
    color: var(--muted);
    text-transform: uppercase;
    margin-top: 2px;
  }
  .divider {
    width: 1px;
    height: 100px;
    background: var(--rule);
    flex: none;
  }
  .contact-list {
    list-style: none;
    padding-left: 26px;
    font-family: "Montserrat", sans-serif;
    font-size: 19px;
    color: var(--white);
  }
  .contact-item {
    display: flex;
    align-items: center;
    gap: 12px;
    line-height: 30px;
    white-space: nowrap;
  }
  .contact-icon { width: 18px; height: 18px; flex: none; }
</style>
</head>
<body>

  <section class="card card-front" aria-label="Card front">
    <div class="brand">
      <span class="brand-dot"></span>
      <span class="brand-name">Brightpaw Obedience</span>
    </div>
    <p class="tagline">“Teaching good manners one happy dog at a time.”</p>
  </section>

  <section class="card card-back" aria-label="Card back">
    <div class="identity">
      <p class="identity-name">Felix Orland</p>
      <p class="identity-role">Owner</p>
    </div>
    <span class="divider"></span>
    <ul class="contact-list">
      <li class="contact-item">
        <svg class="contact-icon" viewBox="0 0 24 24" aria-hidden="true">
          <path fill="#ec1f27" d="M6.6 10.8a15 15 0 0 0 6.6 6.6l2.2-2.2a1 1 0 0 1 1-.25 11.4 11.4 0 0 0 3.6.57 1 1 0 0 1 1 1V20a1 1 0 0 1-1 1A17 17 0 0 1 3 4a1 1 0 0 1 1-1h3.5a1 1 0 0 1 1 1c0 1.250.2 2.45.57 3.6a1 1 0 0 1-.25 1z"/>
        </svg>
        415 903 2276
      </li>
      <li class="contact-item">
        <svg class="contact-icon" viewBox="0 0 24 24" aria-hidden="true">
          <rect x="2.5" y="5" width="19" height="14" fill="none" stroke="#ec1f27" stroke-width="2"/>
          <path d="M3 6l9 7 9-7" fill="none" stroke="#ec1f27" stroke-width="2"/>
        </svg>
        info@brightpawobedience.example
      </li>
      <li class="contact-item">
        <svg class="contact-icon" viewBox="0 0 24 24" aria-hidden="true">
          <g fill="none" stroke="#ec1f27" stroke-width="1.8">
            <circle cx="12" cy="12" r="9.5"/>
            <ellipse cx="12" cy="12" rx="4.2" ry="9.5"/>
            <path d="M2.5 12h19M4 7h16M4 17h16"/>
          </g>
        </svg>
        www.brightpawobedience.example
      </li>
    </ul>
  </section>

</body>
</html>
```